KHL Flyer Design - Sales Flyer

Using our existing black and red color scheme (logo files attached), we want to create an 8.5 x 16" trifold sales flier template (example attached) for our company. Content/copy is not expected—I only need help with the design/layout. I have shared some images of our operations and people for the flier.
For design themes or other content, you can also look at our website (www.kestrelhaul.com) or the attached PowerPoint presentation.
Target Market(s)
Logistics, trucking, storage
Industry/Entity Type
Logistics, trucking, inventory
Look and feel

```html
<!DOCTYPE html>
<html lang="en">
<head>
<meta charset="utf-8">
<title>KHL Trifold Sales Flyer</title>
<link href="https://fonts.googleapis.com/css2?family=Poppins:wght@300;400;500;600;700;800&display=swap" rel="stylesheet">
<style>
:root{
  --red:#e3262b;
  --dark:#2b2b2d;
  --ink:#333335;
  --backdrop:#b3b3b3;
  --paper:#ffffff;
  --fold:#f3f3f3;
  --muted:#555;
}
*{margin:0;padding:0;box-sizing:border-box}
html,body{width:1114px;height:1200px;overflow:hidden}
body{background:var(--backdrop);font-family:'Poppins',sans-serif;color:var(--ink);position:relative}
.spread{position:absolute;left:69px;background:var(--paper);transform:scale(0.6028);transform-origin:0 0;overflow:hidden}
.spread--outside{top:57px;width:1619px;height:858px}
.spread--inside{top:619px;width:1622px;height:860px}
.spread svg.shapes{position:absolute;inset:0;width:100%;height:100%}
.abs{position:absolute}
.brand{font-family:'Poppins',sans-serif;font-weight:800;color:var(--red);font-size:86px;line-height:1;letter-spacing:2px}
.brand--cover{left:0;width:100%;text-align:center}
.section-title{font-weight:700;color:var(--ink);line-height:1.05}
.difference-title{right:1108px;top:210px;font-size:33px;text-align:right}
.difference-rule{left:427px;top:281px;width:81px;height:3px;background:var(--red)}
.value .value-name{font-size:13.5px;font-weight:600;color:var(--red);display:flex;align-items:center;gap:8px;margin-left:-24px}
.value .value-name svg{width:16px;height:17px}
.value p{font-size:13.4px;line-height:15px;color:var(--ink)}
.intro{left:575px;border-left:3px solid var(--red);padding-left:13px;font-size:16.5px;line-height:19px;color:var(--ink);font-weight:500}
.contact{right:581px;text-align:right;color:#fff}
.contact dt{font-size:18px;font-weight:600;line-height:22px}
.contact dd{font-size:19px;font-weight:400;line-height:22px;margin-bottom:16px}
.web{color:#fff;font-size:22px;letter-spacing:4.5px;display:flex;align-items:center;gap:8px;font-weight:400}
.web svg{width:18px;height:18px}
.headline{right:36px;top:633px;text-align:right;color:#fff;font-weight:800;text-transform:uppercase;line-height:1}
.headline span{display:block}
.headline .h-sm{font-size:32px}
.headline .h-lg{font-size:44px;margin:2px 0}
.headline .h-md{font-size:35px;line-height:33px}
.vision-band{left:44px;top:390px;color:#fff;font-weight:800;font-size:33px}
.pillar{width:150px;text-align:center}
.pillar .badge{width:72px;height:72px;border-radius:50%;margin:0 auto 18px;display:flex;align-items:center;justify-content:center}
.pillar .badge svg{width:38px;height:38px}
.pillar h3{font-size:15.5px;font-weight:700;color:var(--ink);margin-bottom:3px}
.pillar p{font-size:12.4px;line-height:13.6px;color:var(--ink)}
.divider{top:473px;height:215px;border-left:2px dotted #999}
.panel-heading{top:42px;font-size:33px;font-weight:700}
.diff{display:flex;gap:10px;width:195px;font-size:12.4px;line-height:13.6px;color:var(--ink)}
.diff svg{flex:0 0 26px;height:26px}
.service{color:#fff}
.service h4{font-size:18px;font-weight:700;line-height:22px;margin-bottom:4px}
.service p{font-size:12.4px;line-height:13.6px;text-align:center}
</style>
</head>
<body>

<!-- OUTSIDE SPREAD -->
<section class="spread spread--outside" aria-label="Outside spread">
  <svg class="shapes" viewBox="0 0 1619 858" aria-hidden="false">
    <defs>
      <linearGradient id="foldShade" x1="0" x2="1"><stop offset="0" stop-color="#ececec"/><stop offset=".25" stop-color="#f7f7f7"/><stop offset="1" stop-color="#f4f4f4"/></linearGradient>
      <linearGradient id="sky" x1="0" y1="0" x2="0" y2="1"><stop offset="0" stop-color="#8fb6d8"/><stop offset=".55" stop-color="#b9b2a2"/><stop offset="1" stop-color="#7a6550"/></linearGradient>
      <linearGradient id="earth" x1="0" y1="0" x2="1" y2="1"><stop offset="0" stop-color="#8c7b68"/><stop offset="1" stop-color="#c8743e"/></linearGradient>
      <linearGradient id="truck" x1="0" y1="0" x2="0" y2="1"><stop offset="0" stop-color="#b7d3ea"/><stop offset="1" stop-color="#8c8b88"/></linearGradient>
      <linearGradient id="yard" x1="0" y1="0" x2="1" y2="1"><stop offset="0" stop-color="#9d8e7a"/><stop offset=".6" stop-color="#6d5c4b"/><stop offset="1" stop-color="#4a3d33"/></linearGradient>
    </defs>
    <rect x="541" y="0" width="541" height="858" fill="url(#foldShade)"/>
    <polygon role="img" aria-label="Photo: loader on a flatbed trailer under blue sky" points="0,0 476,0 291,263 0,263" fill="url(#sky)"/>
    <polygon points="476,0 541,0 421,182 356,182" fill="var(--dark)"/>
    <polygon role="img" aria-label="Photo: aerial view of a loader moving pipe in a yard" points="0,280 234,280 0,605" fill="url(#earth)"/>
    <rect role="img" aria-label="Line illustration: cargo ship, crane, warehouse and delivery trucks" x="0" y="705" width="690" height="124" fill="#f5f5f5"/>
    <rect x="0" y="831" width="720" height="4" fill="var(--dark)"/>
    <polygon points="826,0 1251,0 1226,30 791,30" fill="var(--dark)"/>
    <polygon points="1251,0 1619,0 1619,30 1226,30" fill="var(--red)"/>
    <polygon role="img" aria-label="Photo: white semi truck parked in a yard" points="606,340 891,340 786,502 541,502" fill="url(#truck)"/>
    <polygon role="img" aria-label="Photo: aerial view of a pipe storage yard with trucks and cranes" points="1046,158 1619,158 1311,618 716,618" fill="url(#yard)"/>
    <polygon points="791,633 1316,633 1619,185 1619,858 606,858" fill="var(--red)"/>
    <polygon points="1619,205 1619,255 1445,520 1400,520" fill="var(--dark)"/>
    <polygon points="740,790 1619,790 1619,835 706,835" fill="var(--dark)"/>
    <rect x="1082" y="0" width="6" height="858" fill="#000" opacity=".05"/>
  </svg>

  <h2 class="abs section-title difference-title">The KHL<br>Difference</h2>
  <div class="abs difference-rule"></div>

  <div class="abs value" style="left:278px;top:293px;width:240px">
    <div class="value-name"><svg viewBox="0 0 16 17"><path d="M8 0 16 3v6c0 4-4 7-8 8-4-1-8-4-8-8V3z" fill="var(--red)"/><path d="M4.5 8.5 7 11l4.5-5" stroke="#fff" stroke-width="1.8" fill="none"/></svg>Integrity</div>
    <p>we operate with honesty and transparency, building trust through every interaction. We hold ourselves accountable to our clients, partners, and each other.</p>
  </div>
  <div class="abs value" style="left:212px;top:381px;width:315px">
    <div class="value-name"><svg viewBox="0 0 16 17"><path d="M8 0 16 3v6c0 4-4 7-8 8-4-1-8-4-8-8V3z" fill="var(--red)"/><path d="M4.5 8.5 7 11l4.5-5" stroke="#fff" stroke-width="1.8" fill="none"/></svg>Safety</div>
    <p>safety isn’t just a priority; it’s embedded in everything we do. From planning to delivery, we adhere to strict safety protocols to ensure the protection of people, assets and the environment.</p>
  </div>
  <div class="abs value" style="left:151px;top:471px;width:372px">
    <div class="value-name"><svg viewBox="0 0 16 17"><path d="M8 0 16 3v6c0 4-4 7-8 8-4-1-8-4-8-8V3z" fill="var(--red)"/><path d="M4.5 8.5 7 11l4.5-5" stroke="#fff" stroke-width="1.8" fill="none"/></svg>Customer Focus</div>
    <p>our clients are at the heart of our operations. We customize solutions to fit their unique needs, and our team is always ready to go the extra mile to exceed expectations.</p>
  </div>
  <div class="abs value" style="left:100px;top:546px;width:412px">
    <div class="value-name"><svg viewBox="0 0 16 17"><path d="M8 0 16 3v6c0 4-4 7-8 8-4-1-8-4-8-8V3z" fill="var(--red)"/><path d="M4.5 8.5 7 11l4.5-5" stroke="#fff" stroke-width="1.8" fill="none"/></svg>Reliability</div>
    <p>consistency is key. Our commitment to delivering safe, timely, and accurate logistics solutions means you can depend on us, day in and day out.</p>
  </div>
  <div class="abs value" style="left:54px;top:621px;width:448px">
    <div class="value-name"><svg viewBox="0 0 16 17"><path d="M8 0 16 3v6c0 4-4 7-8 8-4-1-8-4-8-8V3z" fill="var(--red)"/><path d="M4.5 8.5 7 11l4.5-5" stroke="#fff" stroke-width="1.8" fill="none"/></svg>Innovation</div>
    <p>in a fast-paced industry, we stay ahead by embracing technology and innovative solutions. We’re always looking for better, smarter ways to serve our clients.</p>
  </div>

  <div class="abs brand brand--cover" style="left:541px;width:541px;top:50px">KHL</div>
  <div class="abs brand brand--cover" style="left:1082px;width:537px;top:50px">KHL</div>

  <p class="abs intro" style="top:172px;width:390px">We understand that every business is unique. Our team will work closely with you to create custom solutions that meet your specific needs and challenges.</p>
  <p class="abs intro" style="top:260px;width:360px">Partner with us for seamless, reliable, and cost-effective logistics solutions tailored to your business needs.</p>

  <dl class="abs contact" style="top:663px">
    <dt>Phone</dt><dd>(555) 014-7290</dd>
    <dt>Email</dt><dd>contactus@kestrelhaul.com</dd>
  </dl>

  <h1 class="abs headline">
    <span class="h-sm">Logistics</span>
    <span class="h-lg">Redefined</span>
    <span class="h-md">Tailored solutions for</span>
    <span class="h-md">your business needs</span>
  </h1>

  <div class="abs web" style="right:576px;top:798px"><svg viewBox="0 0 20 20"><circle cx="10" cy="10" r="8.5" fill="none" stroke="#fff" stroke-width="1.6"/><ellipse cx="10" cy="10" rx="3.6" ry="8.5" fill="none" stroke="#fff" stroke-width="1.4"/><path d="M1.5 10h17" stroke="#fff" stroke-width="1.4"/></svg>kestrelhaul.com</div>
  <div class="abs web" style="right:43px;top:798px"><svg viewBox="0 0 20 20"><circle cx="10" cy="10" r="8.5" fill="none" stroke="#fff" stroke-width="1.6"/><ellipse cx="10" cy="10" rx="3.6" ry="8.5" fill="none" stroke="#fff" stroke-width="1.4"/><path d="M1.5 10h17" stroke="#fff" stroke-width="1.4"/></svg>kestrelhaul.com</div>
</section>

<!-- INSIDE SPREAD -->
<section class="spread spread--inside" aria-label="Inside spread">
  <svg class="shapes" viewBox="0 0 1622 860">
    <defs>
      <linearGradient id="foldShade2" x1="0" x2="1"><stop offset="0" stop-color="#ececec"/><stop offset=".25" stop-color="#f7f7f7"/><stop offset="1" stop-color="#f4f4f4"/></linearGradient>
      <linearGradient id="worker" x1="0" y1="0" x2="1" y2="1"><stop offset="0" stop-color="#8b8a86"/><stop offset=".5" stop-color="#7a5b45"/><stop offset="1" stop-color="#c9b8a6"/></linearGradient>
      <linearGradient id="pipes" x1="0" y1="0" x2="1" y2="0"><stop offset="0" stop-color="#6b5246"/><stop offset="1" stop-color="#a89383"/></linearGradient>
      <linearGradient id="forklift" x1="0" y1="0" x2="0" y2="1"><stop offset="0" stop-color="#a9aab0"/><stop offset=".5" stop-color="#9a8b57"/><stop offset="1" stop-color="#3d3c3e"/></linearGradient>
      <linearGradient id="svc" x1="0" y1="0" x2="1" y2="1"><stop offset="0" stop-color="#a6a29a"/><stop offset="1" stop-color="#5a4f47"/></linearGradient>
    </defs>
    <rect x="541" y="0" width="541" height="860" fill="url(#foldShade2)"/>
    <polygon points="911,0 1622,0 1622,860 1514,860" fill="var(--dark)"/>
    <polygon points="441,41 511,41 541,88 471,88" fill="var(--red)"/>
    <polygon points="946,41 1011,41 1046,88 981,88" fill="var(--red)"/>
    <polygon points="1026,41 1091,41 1126,88 1061,88" fill="var(--red)"/>
    <polygon role="img" aria-label="Photo: worker in hard hat handling pipe ends on racks" points="0,0 406,0 676,371 0,371" fill="url(#worker)"/>
    <polygon points="0,130 196,371 0,371" fill="var(--red)"/>
    <polygon points="0,371 356,371 403,440 0,440" fill="var(--red)"/>
    <polygon role="img" aria-label="Photo: close view of stacked pipe ends" points="601,235 845,235 920,361 676,361" fill="url(#pipes)"/>
    <polygon role="img" aria-label="Photo: rows of pipe in a storage yard" points="845,235 1090,235 1130,361 920,361" fill="#a89a8e"/>
    <polygon role="img" aria-label="Faded photo: worker walking beside pipe stacks" points="541,375 686,375 946,763 541,763" fill="#ebebeb"/>
    <polygon role="img" aria-label="Photo: yellow loader carrying pipe beside rail cars" points="686,375 1176,375 1446,763 946,763" fill="url(#forklift)"/>
    <polygon role="img" aria-label="Photo: truck with flatbed and forklift" points="1011,110 1196,110 1256,201 1071,201" fill="url(#svc)"/>
    <polygon role="img" aria-label="Photo: aerial view of storage yard" points="1081,211 1286,211 1346,301 1141,301" fill="#6f6a5f"/>
    <polygon role="img" aria-label="Photo: worker transloading pipe" points="1154,313 1361,313 1421,403 1214,403" fill="#8d8478"/>
    <polygon role="img" aria-label="Photo: inspector checking pipe" points="1226,415 1436,415 1496,505 1286,505" fill="#7d6e64"/>
    <polygon points="1306,518 1361,518 1526,748 1622,748 1622,795 1496,795" fill="var(--red)"/>
    <rect role="img" aria-label="Line illustration: warehouse, delivery trucks and loading racks" x="0" y="712" width="700" height="124" fill="#f5f5f5"/>
    <rect x="0" y="837" width="716" height="3" fill="var(--dark)"/>
    <polygon points="716,798 1622,798 1622,843 686,843" fill="var(--dark)"/>
    <rect x="1082" y="0" width="6" height="860" fill="#000" opacity=".05"/>
  </svg>

  <h2 class="abs vision-band">VISION &amp; PURPOSE</h2>

  <div class="abs pillar" style="left:28px;top:469px">
    <div class="badge" style="background:var(--red)"><svg viewBox="0 0 40 40"><path d="M30 8c-7 0-13 5-16 12l6 6c7-3 12-9 12-16z" fill="#fff"/><path d="M14 20l-5 1-3 5 6-1zM20 26l-1 5-5 3 1-6z" fill="#fff"/><circle cx="24" cy="15" r="2.5" fill="var(--red)"/></svg></div>
    <h3>VISION</h3>
    <p>To be the leading provider of innovative and reliable logistics solutions, recognized for unwavering dedication to safety, reliability, and superior customer service.</p>
  </div>
  <div class="abs divider" style="left:199px"></div>
  <div class="abs pillar" style="left:204px;top:469px">
    <div class="badge" style="background:var(--dark)"><svg viewBox="0 0 40 40"><circle cx="20" cy="17" r="9" fill="none" stroke="#fff" stroke-width="2.2"/><circle cx="20" cy="17" r="3.5" fill="#fff"/><path d="M15 28h10M16 32h8" stroke="#fff" stroke-width="2.2"/><path d="M20 3v3M7 8l2 2M33 8l-2 2M4 17h3M33 17h3" stroke="#fff" stroke-width="1.8"/></svg></div>
    <h3>INNOVATION</h3>
    <p>We leverage cutting edge technologies to streamline supply chains and maximize value while keeping it simple–getting your product to the right place at the right time.</p>
  </div>
  <div class="abs divider" style="left:370px"></div>
  <div class="abs pillar" style="left:376px;top:469px">
    <div class="badge" style="background:var(--red)"><svg viewBox="0 0 40 40"><circle cx="16" cy="9" r="4" fill="#fff"/><path d="M9 25v-6a7 7 0 0 1 14 0v6z" fill="#fff"/><circle cx="16" cy="31" r="3.5" fill="none" stroke="#fff" stroke-width="2"/><path d="M28 30V10m-3 3 3-3 3 3" stroke="#fff" stroke-width="2" fill="none"/><path d="M30 4v4M28 6h4" stroke="#fff" stroke-width="1.6"/></svg></div>
    <h3>PEOPLE</h3>
    <p>We are passionate about every job we undertake. You can count on our team to complete each task with integrity, dedication, and enthusiasm.</p>
  </div>

  <h2 class="abs panel-heading" style="left:559px;color:var(--ink)">KEY DIFFERENTIATORS</h2>
  <div class="abs diff" style="left:566px;top:97px"><svg viewBox="0 0 26 26"><path d="M2 14l5-5 6 3 6-3 5 5-7 6-4-3-4 3z" fill="none" stroke="var(--red)" stroke-width="1.3"/></svg><span>Deep industry knowledge and expertise</span></div>
  <div class="abs diff" style="left:768px;top:97px"><svg viewBox="0 0 26 26"><circle cx="13" cy="13" r="11" fill="none" stroke="var(--red)" stroke-width="1.3"/><circle cx="13" cy="13" r="6" fill="none" stroke="var(--red)" stroke-width="1.3"/><circle cx="13" cy="13" r="1.6" fill="var(--red)"/></svg><span>Monthly cycle counts and spot checks</span></div>
  <div class="abs diff" style="left:566px;top:140px"><svg viewBox="0 0 26 26"><circle cx="13" cy="11" r="6.5" fill="none" stroke="var(--red)" stroke-width="1.3"/><path d="M10 20h6M11 23h4" stroke="var(--red)" stroke-width="1.3"/><path d="M10.5 11l2 2 3-4" stroke="var(--red)" stroke-width="1.3" fill="none"/></svg><span>High volume operation with sustained delivery and inventory accuracy performance &gt;99%</span></div>
  <div class="abs diff" style="left:768px;top:140px"><svg viewBox="0 0 26 26"><rect x="4" y="3" width="15" height="20" rx="1.5" fill="none" stroke="var(--red)" stroke-width="1.3"/><path d="M7 8h9M7 12h5" stroke="var(--red)" stroke-width="1.3"/><circle cx="17" cy="17" r="3.5" fill="none" stroke="var(--red)" stroke-width="1.3"/><path d="M19.5 19.5l3 3" stroke="var(--red)" stroke-width="1.3"/></svg><span>Quarterly business reviews (QBRs) and monthly inventory reporting</span></div>

  <h2 class="abs panel-heading" style="left:1131px;color:#fff">SERVICES</h2>
  <div class="abs service" style="left:1209px;top:111px;width:380px">
    <h4>Transportation &amp; Forklift/Crane Rentals</h4>
    <p>From forklifts to trucking, transloading to inspection, we have top-quality options that support you at each step of the process.</p>
  </div>
  <div class="abs service" style="left:1278px;top:207px;width:330px">
    <h4>Storage</h4>
    <p>Our customized storage solutions let you expand your market reach and strategically position inventory for lower freight costs and efficient distribution.</p>
  </div>
  <div class="abs service" style="left:1348px;top:310px;width:262px">
    <h4>Transloading</h4>
    <p>Our comprehensive logistics services cover every aspect of rail transportation, from the point of origin to the final destination.</p>
  </div>
  <div class="abs service" style="left:1419px;top:408px;width:200px">
    <h4>Inspection</h4>
    <p>Trust us to ensure the reliability and safety of your OCTG material. We ensure your product is free from defects by performing both visual and non-destructive testing (NDT).</p>
  </div>

  <div class="abs brand" style="left:658px;top:662px;font-size:80px">KHL</div>

  <div class="abs web" style="right:579px;top:808px"><svg viewBox="0 0 20 20"><circle cx="10" cy="10" r="8.5" fill="none" stroke="#fff" stroke-width="1.6"/><ellipse cx="10" cy="10" rx="3.6" ry="8.5" fill="none" stroke="#fff" stroke-width="1.4"/><path d="M1.5 10h17" stroke="#fff" stroke-width="1.4"/></svg>kestrelhaul.com</div>
  <div class="abs web" style="right:129px;top:808px"><svg viewBox="0 0 20 20"><circle cx="10" cy="10" r="8.5" fill="none" stroke="#fff" stroke-width="1.6"/><ellipse cx="10" cy="10" rx="3.6" ry="8.5" fill="none" stroke="#fff" stroke-width="1.4"/><path d="M1.5 10h17" stroke="#fff" stroke-width="1.4"/></svg>kestrelhaul.com</div>
</section>

</body>
</html>
```